B2B flyer solution for charging infrastructures (One-Pager Din A4, double-sided)

We need a professional design for our flyer in format Din A4/both sides.
Attached you will find the content for the flyer, but we are looking for a modern, professional design.

Some background/context information:
- the product is about a solution for charging and billing of charging infrastructures (for electric cars) in companies
- target group: companies, esp. facility managers, fleet managers, controlling, CTO, CEO
- should be printed and available online
- our website (and most of our current design work): https://wendavo-netz.de

In the files you will find:
- photos of reference implementations of our solution (should be included in the flyer)
- stock photos (we are using the one you will find in the current flyer on our presentations, maybe you can use it too to keep some corporate identity.
- our logo
- the current flyer as PDF and as PowerPoint
- a sample presentation we also need for customer communication

It would be nice if the design will align with the existing design work, but bring fresh aspects and will be up-to-date and professional.

Target Market(s)

B2B, companies, fleet managers, facility managers, CTO, CIO

Industry/Entity Type

Enterprises, Charging Solutions for Electric Vehicles

Requirements
Nice to have
• Bright, light design, clean, readable

```html
<!DOCTYPE html>
<html lang="de">
<head>
<meta charset="utf-8">
<title>WENDAVO Professional – Flyer</title>
<link href="https://fonts.googleapis.com/css2?family=Bebas+Neue&family=Montserrat:wght@400;500;600;700;800&display=swap" rel="stylesheet">
<style>
  :root{
    --bg:#d4d5d7;
    --paper:#ffffff;
    --pink:#e0359a;
    --purple:#7b62b8;
    --ink:#111111;
    --text:#222222;
    --grad:linear-gradient(90deg,var(--pink),var(--purple));
  }
  *{margin:0;padding:0;box-sizing:border-box}
  html,body{width:1200px;height:829px;overflow:hidden;background:var(--bg)}
  body{font-family:"Montserrat",sans-serif;color:var(--text);position:relative}
  .page{position:absolute;top:58px;width:484px;height:684px;background:var(--paper);overflow:hidden}
  .page--front{left:71px}
  .page--back{left:645px}
  .decor{position:absolute;inset:0}
  .abs{position:absolute}

  .brand{left:30px;top:60px;display:flex;align-items:center;gap:8px;font-weight:600;font-size:19px;color:var(--ink)}
  .brand__dot{width:14px;height:14px;border-radius:50%;background:var(--pink)}

  .title{font-family:"Bebas Neue",sans-serif;line-height:.8;letter-spacing:.2px}
  .title__pink{color:var(--pink);display:block}
  .title__black{color:var(--ink);display:block}
  .front .title{left:18px;top:124px;font-size:44px}

  .subtitle{left:18px;top:197px;font-size:9.4px;font-weight:600;line-height:11.5px;color:var(--ink)}

  .band{left:0;top:230px;width:287px;height:43px;background:var(--grad);color:#fff;font-size:10.6px;font-weight:600;line-height:12px;padding:4px 0 0 18px}
  .lead{left:18px;top:282px;font-size:10.4px;font-weight:600;line-height:12px;color:var(--ink)}

  .heading{color:var(--pink);font-weight:700;font-size:12.5px;white-space:nowrap}
  .list{list-style:none;font-size:8.6px;line-height:10.2px;color:var(--text)}
  .list li{position:relative;padding-left:17px;margin-bottom:2.4px}
  .list li::before{content:"";position:absolute;left:1px;top:2px;width:10px;height:5px;border:1.6px solid var(--purple);border-radius:3px}

  .pill-dark{left:0;top:542px;width:159px;height:18px;background:var(--ink);color:#fff;font-weight:700;font-size:12.5px;line-height:18px;padding-left:12px;border-radius:0 9px 9px 0}
  .contact-text{left:12px;top:561px;font-size:10px;line-height:11.5px;color:var(--ink)}
  .pill-grad{left:0;top:602px;width:217px;height:18px;background:var(--grad);color:#fff;font-weight:700;font-size:12.5px;line-height:18px;padding-left:12px;border-radius:0 9px 9px 0}
  .contact-list{left:12px;top:622px;font-size:10px;line-height:11.5px;color:var(--ink)}

  .back .title{left:22px;top:25px}
  .back .title__pink{font-size:50px}
  .back .title__black{font-size:54px}
  .pill-sub{left:21px;top:113px;width:171px;height:17px;background:var(--grad);color:#fff;font-weight:600;font-size:11px;line-height:17px;padding-left:8px;border-radius:9px}

  .band-back{left:0;top:391px;width:325px;height:20px;background:var(--grad);color:#fff;font-weight:700;font-size:15px;line-height:20px;padding-left:19px;border-radius:0 10px 10px 0}
  .section{left:21px;width:345px}
  .section .heading{font-size:11.6px;line-height:14px;margin-bottom:2px}
  .section p{font-size:8.3px;line-height:12.4px;color:var(--text);white-space:nowrap}

  .audience{left:376px;width:104px;text-align:center}
  .audience__box{width:61px;height:61px;margin:0 auto;border:1.6px solid var(--pink);border-bottom-color:var(--purple);border-radius:3px;display:flex;align-items:center;justify-content:center}
  .audience__label{margin-top:13px;font-size:9.6px;font-weight:700;line-height:10.4px;color:var(--ink)}

  .footer-band{left:0;top:660px;width:484px;height:16px;background:var(--grad);color:#fff;font-size:9.6px;line-height:16px;display:flex;justify-content:space-around;padding:0 10px 0 25px;white-space:nowrap}
</style>
</head>
<body>

<section class="page page--front front">
  <svg class="decor" viewBox="0 0 484 684" width="484" height="684">
    <defs>
      <linearGradient id="fGrad" x1="0" y1="0" x2="1" y2="0">
        <stop offset="0" stop-color="#e0359a"/><stop offset="1" stop-color="#7b62b8"/>
      </linearGradient>
      <linearGradient id="fPhotoA" x1="0" y1="0" x2="1" y2="1">
        <stop offset="0" stop-color="#b7a892"/><stop offset=".5" stop-color="#7e7368"/><stop offset="1" stop-color="#c9b9ad"/>
      </linearGradient>
      <linearGradient id="fPhotoB" x1="0" y1="0" x2="0" y2="1">
        <stop offset="0" stop-color="#c9a063"/><stop offset=".55" stop-color="#6f8a4a"/><stop offset="1" stop-color="#8c8f86"/>
      </linearGradient>
      <linearGradient id="fCharger" x1="0" y1="0" x2="1" y2="0">
        <stop offset="0" stop-color="#e6e6ea"/><stop offset="1" stop-color="#f7f7f9"/>
      </linearGradient>
    </defs>
    <circle cx="427" cy="114" r="221" fill="url(#fGrad)"/>
    <circle role="img" aria-label="Foto: Ladekabel an einer Ladestation, Frau im Hintergrund" cx="427" cy="114" r="216" fill="url(#fPhotoA)"/>
    <circle cx="418" cy="360" r="140" fill="url(#fGrad)"/>
    <circle role="img" aria-label="Foto: Wallboxen auf Stelen im Freien" cx="418" cy="360" r="135" fill="url(#fPhotoB)"/>
    <circle cx="484" cy="723" r="266" fill="url(#fGrad)"/>
    <rect role="img" aria-label="Produktbild: Schnellladesäule mit zwei Ladekabeln und Ladestele" x="300" y="420" width="148" height="250" rx="6" fill="url(#fCharger)" opacity=".92"/>
  </svg>

  <div class="abs brand"><span class="brand__dot"></span>wendavo-netz.de</div>

  <h1 class="abs title"><span class="title__pink">WENDAVO</span><span class="title__black">PROFESSIONAL</span></h1>
  <p class="abs subtitle">die maßgeschneiderte B2B<br>Abrechnungslösung für Elektromobilität</p>

  <div class="abs band">Lade-Infrastruktur-Abrechnungslösungen<br>für Unternehmen,&nbsp; damit Lade-Infrastruktur<br>Erträge statt Kosten produziert.</div>

  <p class="abs lead">So wird Lade-Infrastruktur von einer<br>Kostenstelle zu einem Profitcenter.</p>

  <h2 class="abs heading" style="left:18px;top:325px">Leistungen:</h2>
  <ul class="abs list" style="left:18px;top:349px;width:290px">
    <li>Vielseitige Abrechnungsmöglichkeiten für<br>Fuhrpark, Mitarbeiter, Partnerunternehmen,<br>Mieter, Kunden und andere.</li>
    <li>Full-Service-Betreuung (Monitoring,<br>Abrechnung, Benutzerbetreuung)</li>
    <li>Integration in ihre Unternehmensabläufe</li>
    <li>Berücksichtigung von Eigentümer/Mieter-Konstellationen</li>
  </ul>

  <h2 class="abs heading" style="left:18px;top:440px">Mit wendavo-netz Professional profitieren:</h2>
  <ul class="abs list" style="left:18px;top:464px;width:230px">
    <li>· Effizienter Verwaltung von Lade-Infrastruktur</li>
    <li>· Umfassende Full-Service-Betreuung</li>
    <li>· Nahtloser Integration in Ihre kaufmännischen Prozesse</li>
    <li>· Vielseitigen Abrechnungsmöglichkeiten</li>
  </ul>

  <div class="abs pill-dark">Kontaktieren Sie uns</div>
  <p class="abs contact-text">Erfahren Sie mehr über wendavo-netz<br>und wie wir Ihre&nbsp; Abrechnungsanforderungen<br>erfüllen können.</p>
  <div class="abs pill-grad">für eine kostenlose Beratung:</div>
  <p class="abs contact-list">Telefon: +49 (0) 1111 222 333<br>E-Mail: info@wendavo-netz.de<br>Web: www.wendavo-netz.de</p>
</section>

<section class="page page--back back">
  <svg class="decor" viewBox="0 0 484 684" width="484" height="684">
    <defs>
      <linearGradient id="bGrad" x1="0" y1="0" x2="1" y2="1">
        <stop offset="0" stop-color="#e0359a"/><stop offset="1" stop-color="#7b62b8"/>
      </linearGradient>
      <linearGradient id="bPhoto" x1="0" y1="0" x2="1" y2="1">
        <stop offset="0" stop-color="#3a3d3a"/><stop offset=".6" stop-color="#4f6b3c"/><stop offset="1" stop-color="#d8d8d8"/>
      </linearGradient>
      <linearGradient id="bProduct" x1="0" y1="0" x2="1" y2="0">
        <stop offset="0" stop-color="#e9eaec"/><stop offset=".5" stop-color="#f4f5f6"/><stop offset="1" stop-color="#e4e8ea"/>
      </linearGradient>
    </defs>
    <circle cx="372" cy="93" r="112" fill="url(#bGrad)"/>
    <circle role="img" aria-label="Foto: Ladesäule mit weißem Elektroauto" cx="372" cy="93" r="107" fill="url(#bPhoto)"/>
    <rect role="img" aria-label="Produktbild: Ladesäulen neben einem weißen Elektro-SUV" x="0" y="150" width="368" height="216" rx="4" fill="url(#bProduct)"/>
  </svg>

  <h1 class="abs title"><span class="title__pink">WENDAVO</span><span class="title__black">PROFESSIONAL</span></h1>
  <div class="abs pill-sub">die Funktionen im Überblick</div>

  <div class="abs band-back">Verrechnung von Ladevorgängen für:</div>

  <div class="abs section" style="top:416px">
    <h2 class="heading">Full-Service-Betreuung für sorgenfreies&nbsp; Management</h2>
    <p>wendavo-netz übernimmt auf Wunsch alle&nbsp; organisatorischen Belange bei<br>der Verwaltung&nbsp; Ihrer Lade-Infrastruktur, einschließlich:<br>· Monitoring<br>· Support<br>· User-Onboarding und -Support<br>· Handling von Zugangskarten<br>· Integration von firmeninternen Zugangstoken</p>
  </div>

  <div class="abs section" style="top:528px">
    <h2 class="heading">Perfekte Integration in kaufmännische Prozesse</h2>
    <p>wendavo-netz fügt sich nahtlos in die kaufmännischen&nbsp; Strukturen moderner<br>Unternehmen ein und bietet:<br>· Erweitertes Reporting<br>· Aufschlüsselung und Tarifierung nach&nbsp; Nutzergruppe<br>· Unterstützung unternehmensinterner Abrechnung und Verrechnung<br>&nbsp;&nbsp;und/oder Zahlungseinzug durch&nbsp; wendavo-netz<br>· Schnittstellen zu Buchhaltung und Lohnbuchhaltung<br>· Bedarfsgerechte Anpassbarkeit</p>
  </div>

  <div class="abs audience" style="top:230px">
    <div class="audience__box">
      <svg width="48" height="20" viewBox="0 0 48 20" aria-hidden="true">
        <g fill="#222"><path d="M2 12l3-6h10l3 6v4H2z"/><path d="M16 11l3-7h10l3 7v5H16z"/><path d="M30 12l3-6h10l3 6v4H30z"/></g>
        <g fill="#fff"><rect x="20" y="6" width="8" height="4"/></g>
        <g fill="#222"><circle cx="6" cy="17" r="2"/><circle cx="14" cy="17" r="2"/><circle cx="20" cy="17" r="2"/><circle cx="28" cy="17" r="2"/><circle cx="34" cy="17" r="2"/><circle cx="42" cy="17" r="2"/></g>
      </svg>
    </div>
    <p class="audience__label">Fuhrpark,<br>Dienstwagen</p>
  </div>
  <div class="abs audience" style="top:336px">
    <div class="audience__box">
      <svg width="44" height="28" viewBox="0 0 44 28" aria-hidden="true" fill="#222">
        <circle cx="9" cy="6" r="4"/><circle cx="35" cy="6" r="4"/><circle cx="22" cy="10" r="5"/>
        <path d="M1 20a8 7 0 0 1 16 0z"/><path d="M27 20a8 7 0 0 1 16 0z"/><path d="M11 28a11 10 0 0 1 22 0z"/>
      </svg>
    </div>
    <p class="audience__label">Mitarbeiter<br>Privatfahrzeuge</p>
  </div>
  <div class="abs audience" style="top:443px">
    <div class="audience__box">
      <svg width="38" height="42" viewBox="0 0 38 42" aria-hidden="true" fill="#222">
        <circle cx="8" cy="4" r="3"/><circle cx="19" cy="4" r="3"/><circle cx="30" cy="4" r="3"/>
        <rect x="5" y="8" width="6" height="8" rx="2"/><rect x="16" y="8" width="6" height="8" rx="2"/><rect x="27" y="8" width="6" height="8" rx="2"/>
        <circle cx="13" cy="19" r="3"/><circle cx="25" cy="19" r="3"/>
        <rect x="10" y="23" width="6" height="9" rx="2"/><rect x="22" y="23" width="6" height="9" rx="2"/>
        <circle cx="19" cy="30" r="3"/><rect x="16" y="34" width="6" height="8" rx="2"/>
      </svg>
    </div>
    <p class="audience__label">Kunden und<br>Gäste</p>
  </div>
  <div class="abs audience" style="top:549px">
    <div class="audience__box">
      <svg width="40" height="32" viewBox="0 0 40 32" aria-hidden="true" fill="#222">
        <rect x="2" y="12" width="11" height="20"/><rect x="14" y="2" width="11" height="30"/><rect x="27" y="8" width="11" height="24"/>
        <g fill="#fff"><rect x="4" y="15" width="3" height="3"/><rect x="8" y="15" width="3" height="3"/><rect x="4" y="21" width="3" height="3"/><rect x="8" y="21" width="3" height="3"/>
        <rect x="16" y="5" width="3" height="3"/><rect x="20" y="5" width="3" height="3"/><rect x="16" y="11" width="3" height="3"/><rect x="20" y="11" width="3" height="3"/><rect x="16" y="17" width="3" height="3"/><rect x="20" y="17" width="3" height="3"/>
        <rect x="29" y="11" width="3" height="3"/><rect x="33" y="11" width="3" height="3"/><rect x="29" y="17" width="3" height="3"/><rect x="33" y="17" width="3" height="3"/></g>
      </svg>
    </div>
    <p class="audience__label">Vermieter,<br>Eigentümer</p>
  </div>

  <div class="abs footer-band">
    <span>Telefon: +49 (0) 1111 222 333</span>
    <span>E-Mail: info@wendavo-netz.de</span>
    <span>Web: www.wendavo-netz.de</span>
  </div>
</section>

</body>
</html>
```